A card that says it all!

Hey there!
We are in need of a business card design for a facility service provider company named Dovra Works.
I would like a business card design that is not focus on a person but more on the company. A place for a QR code would be nice, and i will have that code direct to our request form online. "Scanner to schedule service" or "Scan to schedule a estimate". Something like that. Dovra Works is the Industry Leader in Facility Remodeling, Rollouts, and Capital Repairs

Target Market(s)

large facilities needing services such as remodels. HVAC, plumbing, electrical

Industry/Entity Type

Industry Leader in Facility Remodeling, Rollouts, and Capital Repairs

Contact Information for Business Card

phone number: 517.382.9064; email: info@dovraworks.example; Website: www.DovraWorks.example

Requirements
Must have
• sleak; classic
Should not have
• No houses or tools art

```html
<!DOCTYPE html>
<html lang="en">
<head>
<meta charset="utf-8">
<title>Dovra Works — Business Card</title>
<link rel="stylesheet" href="https://fonts.googleapis.com/css2?family=Old+Standard+TT:wght@700&family=Montserrat:wght@400&display=swap">
<style>
  :root {
    --backdrop: #9a9a9a;
    --brand-blue: #164a9c;
    --paper: #ffffff;
    --ink: #1a1a1a;
    --card-shadow: rgba(0, 0, 0, 0.45);
  }
  html, body {
    margin: 0;
    padding: 0;
    width: 1093px;
    height: 1200px;
    overflow: hidden;
    background: var(--backdrop);
  }
  .canvas {
    position: relative;
    width: 1093px;
    height: 1200px;
  }
  .card {
    position: absolute;
    left: 264px;
    width: 597px;
    box-shadow: 0 1px 3px var(--card-shadow);
    overflow: hidden;
  }
  .card--front {
    top: 224px;
    height: 364px;
    background: var(--paper);
  }
  .card--back {
    top: 616px;
    height: 366px;
    background: var(--brand-blue);
  }
  .front__band {
    position: absolute;
    left: 0;
    bottom: 0;
    width: 100%;
    height: 16px;
    background: var(--brand-blue);
  }
  .wordmark {
    position: absolute;
    display: flex;
    align-items: center;
    justify-content: center;
    font-family: "Old Standard TT", Georgia, serif;
    font-weight: 700;
    white-space: nowrap;
    letter-spacing: 0.01em;
  }
  .wordmark--front {
    left: 100px;
    top: 163px;
    width: 193px;
    height: 86px;
    font-size: 31px;
    color: var(--brand-blue);
  }
  .wordmark--back {
    left: 96px;
    top: 92px;
    width: 404px;
    height: 183px;
    font-size: 66px;
    color: var(--paper);
  }
  .front__divider {
    position: absolute;
    left: 302px;
    top: 151px;
    width: 1px;
    height: 109px;
    background: var(--brand-blue);
  }
  .contact-block {
    position: absolute;
    left: 309px;
    top: 147px;
  }
  .contact-block__name {
    margin: 0;
    font-family: "Old Standard TT", Georgia, serif;
    font-weight: 700;
    font-size: 23px;
    line-height: 24px;
    color: var(--brand-blue);
    letter-spacing: 0;
    padding-left: 1px;
    white-space: nowrap;
  }
  .contact-block__title {
    margin: 2px 0 0;
    font-family: "Montserrat", Arial, sans-serif;
    font-size: 14px;
    line-height: 18px;
    color: var(--ink);
  }
  .contact-list {
    list-style: none;
    margin: 8px 0 0;
    padding: 0;
  }
  .contact-list__item {
    display: flex;
    align-items: center;
    height: 23px;
    font-family: "Montserrat", Arial, sans-serif;
    font-size: 14px;
    color: var(--ink);
    white-space: nowrap;
  }
  .contact-list__icon {
    width: 13px;
    height: 13px;
    margin: 0 8px 0 5px;
    fill: var(--brand-blue);
    flex: none;
  }
</style>
</head>
<body>
<main class="canvas">
  <section class="card card--front" aria-label="Card front">
    <div class="wordmark wordmark--front">Dovra Works</div>
    <div class="front__divider"></div>
    <div class="contact-block">
      <h1 class="contact-block__name">MARLEN TOBIAS</h1>
      <p class="contact-block__title">Managing Director</p>
      <ul class="contact-list">
        <li class="contact-list__item">
          <svg class="contact-list__icon" viewBox="0 0 24 24" aria-hidden="true"><path d="M6.6 10.8c1.4 2.8 3.8 5.1 6.6 6.6l2.2-2.2c.3-.3.7-.4 1-.2 1.1.4 2.3.6 3.6.6.6 0 1 .4 1 1V20c0 .6-.4 1-1 1C10.6 21 3 13.4 3 4c0-.6.4-1 1-1h3.5c.6 0 1 .4 1 1 0 1.3.2 2.5.6 3.6.1.3 0 .7-.2 1z"/></svg>
          517.382.9064
        </li>
        <li class="contact-list__item">
          <svg class="contact-list__icon" viewBox="0 0 24 24" aria-hidden="true"><path d="M2 5h20v2l-10 6L2 7z"/><path d="M2 9l10 6 10-6v10H2z"/></svg>
          info@dovraworks.example
        </li>
        <li class="contact-list__item">
          <svg class="contact-list__icon" viewBox="0 0 24 24" aria-hidden="true"><circle cx="12" cy="12" r="10" fill="none" stroke="#164a9c" stroke-width="2.4"/><path d="M2 12h20M12 2c3 3 3 17 0 20M12 2c-3 3-3 17 0 20" fill="none" stroke="#164a9c" stroke-width="1.8"/></svg>
          www.DovraWorks.example
        </li>
      </ul>
    </div>
    <div class="front__band"></div>
  </section>

  <section class="card card--back" aria-label="Card back">
    <div class="wordmark wordmark--back">Dovra Works</div>
  </section>
</main>
</body>
</html>
```